Upscale business cards needed for Board of Directors

We need professional business cards created for members of our family business Board of Directors. We would like these relatively simple and straightforward, but also with a unique element to set them apart. Probably stick with neutral and simple colors - white, grey etc. We need space for the traditional elements, including name, title, address, email/phone number. And we will be creating several from this template so it needs to be template that is easy to switch information in and out of.
Business
See description

```html
<!DOCTYPE html>
<html lang="en">
<head>
<meta charset="utf-8">
<title>Keystone Holdings – Business Cards</title>
<link href="https://fonts.googleapis.com/css2?family=Source+Sans+3:wght@400;600&display=swap" rel="stylesheet">
<style>
  :root {
    --page-bg: #4a4a4a;
    --card-bg: #333233;
    --name-white: #ffffff;
    --gold: #b49c70;
    --text-muted: #a6a3a0;
    --rule: #55524f;
  }
  * { margin: 0; padding: 0; box-sizing: border-box; }
  html, body {
    width: 1200px;
    height: 1000px;
    overflow: hidden;
    background: var(--page-bg);
  }
  .canvas {
    position: relative;
    width: 1200px;
    height: 1000px;
  }
  .card {
    position: absolute;
    left: 287px;
    width: 626px;
    height: 358px;
    background: var(--card-bg);
    box-shadow: 0 6px 16px rgba(0,0,0,0.35);
    text-align: center;
    font-family: "Source Sans 3", "Myriad Pro", sans-serif;
  }
  .card--front { top: 140px; }
  .card--back { top: 531px; }

  .accent-bar {
    position: absolute;
    background: var(--gold);
  }
  .card--front .accent-bar { left: 130px; top: 125px; width: 368px; height: 6px; }
  .card--back .accent-bar { left: 158px; top: 63px; width: 311px; height: 5px; }

  .company-name {
    position: absolute;
    left: 0;
    right: 0;
    font-weight: 600;
    color: var(--name-white);
    text-transform: uppercase;
    line-height: 1;
  }
  .card--front .company-name { top: 160px; font-size: 38px; letter-spacing: 2px; }
  .card--back .company-name { top: 102px; font-size: 32px; letter-spacing: 2px; }

  .card__url {
    position: absolute;
    left: 0;
    right: 0;
    top: 308px;
    font-size: 14px;
    color: var(--text-muted);
  }

  .contact {
    position: absolute;
    left: 0;
    right: 0;
    top: 200px;
    color: var(--text-muted);
    font-size: 14px;
  }
  .contact__person {
    display: inline-block;
    padding: 0 6px 10px;
    border-bottom: 1px solid var(--rule);
  }
  .contact__name {
    font-size: 17px;
    font-weight: 600;
    color: var(--gold);
  }
  .contact__divider { margin: 0 8px; color: var(--text-muted); }
  .contact__title { font-size: 14px; }
  .contact__address { margin-top: 11px; }
  .contact__lines { margin-top: 6px; line-height: 20px; }
  .contact__label { color: var(--gold); }
</style>
</head>
<body>
<main class="canvas">
  <section class="card card--front">
    <div class="accent-bar"></div>
    <p class="company-name">Keystone Holdings</p>
    <p class="card__url">www.keystoneholdings.com</p>
  </section>

  <section class="card card--back">
    <div class="accent-bar"></div>
    <p class="company-name">Keystone Holdings</p>
    <div class="contact">
      <div class="contact__person">
        <span class="contact__name">Daniel Moore</span><span class="contact__divider">|</span><span class="contact__title">Founder</span>
      </div>
      <p class="contact__address">Street name, Suite 100 State, Zip Code, Country</p>
      <p class="contact__lines">
        <span class="contact__label">P</span> : 012-345-6789 <span class="contact__divider">|</span> <span class="contact__label">E</span> : info@keystoneholdings.com<br>
        www.keystoneholdings.com
      </p>
    </div>
  </section>
</main>
</body>
</html>
```